Modern book cover design

We are looking for a modern, powerful book cover for a general intrest book about how robots are going to take human jobs in the future.

The book title is "Gearstorm"

It also has a strap line "The end of human jobs and how robots will replace them"
Both the title and the strap line should be on the front cover

I have attached a number of book designs I like, and my author picture.
Updates

Reason: Some great submissions but none quite have that wow factor

Target Market(s)

This is a general intrest book, but the reader is likely to be male 30-50

Requirements
Must have
• -Title "Gearstorm"

-Strap-line "The end of human jobs and how robots will replace them"

-Be compliant with PressNook Cover Design Criteria(www.pressnook-example.com)

-Book size : 5.5 x 8.5 inches

-Spine size : 0.625 inches

-Must have one author picture on the back cover(attached)

-Must have the following author description on back cover:
"Tom Hale is a leading futurologist, technologist, inventor, and entrepreneur. With over twenty years of experience in technology and innovation, Tom has travelled the world seeking out and developing new technologies. As a leading voice on the challenges and benefits of tomorrow’s technology, he has advised some of the world’s leading institutions, including the Amber Hall, regarding technological preparations for the future. He is the recipient of the millennium entrepreneur of the year award and has appeared on numerous technology and philanthropy television programs, as well as presenting Steel Dawn Weekly on Robotics."

-Must have the following book description on back cover:
“Gearstorm is a look at the rapidly changing face of robotics and how it will revolutionize employment over the next thirty years. Tom Hale lays out the arguments in favor of and against the mechanization of our society, as well as the advantages and untold risks as we march into this ever-present future.”

-Must have the following quote on the back cover:
"A fascinating look into the future of robotics and their impact on humanity, be prepared to question when robots will replace you - Derek Lansford, Professor of Cybernetics at the University of Elmsworth”

-Example barcode

```html
<!DOCTYPE html>
<html lang="en">
<head>
<meta charset="utf-8">
<title>Gearstorm – Book Cover</title>
<link rel="stylesheet" href="https://fonts.googleapis.com/css2?family=Anton&family=Cinzel:wght@400;600&family=Orbitron:wght@500&family=Tinos:ital,wght@0,400;1,400;1,700&family=Marcellus+SC&family=Oswald:wght@600&display=swap">
<style>
  :root {
    --page: #ffffff;
    --black: #000000;
    --red: #ff0000;
    --white: #ffffff;
    --panel-blue: #3e6f9b;
    --spine-yellow: #f2c200;
    --spine-orange: #e24a00;
    --night: #0b0f3a;
  }
  html, body {
    margin: 0; padding: 0;
    width: 1200px; height: 1000px;
    overflow: hidden;
    background: var(--page);
  }
  .canvas { position: relative; width: 1200px; height: 1000px; }
  .cover {
    position: absolute; left: 92px; top: 108px;
    width: 1043px; height: 771px;
    background: var(--black);
  }
  /* Back cover */
  .back { position: absolute; left: 0; top: 0; width: 498px; height: 771px; }
  .section-title {
    font-family: "Orbitron", sans-serif; font-weight: 500;
    color: var(--red); letter-spacing: 4px; font-size: 18px; margin: 0;
  }
  .about-book .section-title { position: absolute; left: 0; width: 498px; top: 34px; text-align: center; }
  .book-blurb {
    position: absolute; left: 26px; width: 446px; top: 56px; margin: 0;
    font-family: "Tinos", serif; font-size: 14px; line-height: 17.5px;
    color: var(--white); text-align: center;
  }
  .quote {
    position: absolute; left: 26px; width: 446px; top: 164px; margin: 0;
    font-family: "Tinos", serif; font-style: italic; font-size: 14.5px; line-height: 18px;
    color: var(--white);
  }
  .quote cite { font-weight: 700; font-size: 13.5px; display: block; }
  .author-photo { position: absolute; left: 26px; top: 330px; width: 111px; height: 159px; }
  .about-author .section-title { position: absolute; left: 150px; top: 412px; font-size: 17px; letter-spacing: 3px; }
  .author-name-back {
    position: absolute; left: 143px; top: 428px; margin: 0;
    font-family: "Cinzel", serif; font-weight: 400; font-size: 56px; line-height: 62px;
    color: var(--white); letter-spacing: 1px;
  }
  .author-panel {
    position: absolute; left: 0; top: 489px; width: 498px; height: 182px;
    background: var(--panel-blue); box-sizing: border-box; padding: 3px 30px 0 10px;
  }
  .author-panel p {
    margin: 0; font-family: "Tinos", serif; font-size: 14px; line-height: 17.5px;
    color: var(--white); text-align: justify; text-indent: 8px;
  }
  /* Spine */
  .spine {
    position: absolute; left: 498px; top: 0; width: 45px; height: 771px;
  }
  .spine-text {
    position: absolute; left: 45px; top: 0; width: 771px; height: 45px;
    transform-origin: 0 0; transform: rotate(90deg);
  }
  .spine-text > span { position: absolute; top: 0; height: 45px; display: flex; align-items: center; }
  .spine-title {
    left: 20px; width: 200px;
    font-family: "Oswald", sans-serif; font-weight: 600; font-size: 28px; letter-spacing: 3px;
    white-space: nowrap; line-height: 1;
  }
  .spine-title b {
    font-weight: 600;
    background: linear-gradient(to bottom, var(--spine-yellow), var(--spine-orange));
    -webkit-background-clip: text; background-clip: text; color: transparent;
  }
  .spine-author {
    left: 237px; width: 250px;
    font-family: "Oswald", sans-serif; font-weight: 600; font-size: 27px; letter-spacing: 20px;
    color: var(--white); white-space: nowrap;
  }
  .spine-strap {
    left: 500px; width: 258px; justify-content: center; text-align: center;
    font-family: "Cinzel", serif; font-size: 12px; line-height: 15px; color: var(--white);
  }
  /* Front cover */
  .front { position: absolute; left: 543px; top: 0; width: 500px; height: 771px; overflow: hidden; }
  .cover-art {
    position: absolute; left: 0; top: 170px; width: 500px; height: 601px;
    background:
      radial-gradient(ellipse 60% 40% at 50% 42%, rgba(200,210,255,0.9) 0%, rgba(111,127,240,0.6) 30%, rgba(40,40,140,0) 70%),
      radial-gradient(ellipse 90% 50% at 50% 80%, #6a5aa8 0%, #2a2a7a 55%, var(--night) 100%),
      linear-gradient(to bottom, var(--black), var(--night));
  }
  .front-title {
    position: absolute; left: 0; width: 500px; top: 18px; margin: 0;
    font-family: "Anton", sans-serif; font-weight: 400; font-size: 104px; line-height: 150px;
    color: var(--red); text-align: center; letter-spacing: 0;
  }
  .strap {
    position: absolute; left: 0; width: 500px; top: 566px; margin: 0;
    font-family: "Marcellus SC", serif; font-size: 23px; line-height: 32px;
    color: var(--white); text-align: center; text-shadow: 0 0 4px #000;
  }
  .rule { position: absolute; left: 37px; top: 639px; width: 440px; height: 4px; background: var(--black); }
  .front-author {
    position: absolute; left: 0; width: 500px; top: 668px; margin: 0;
    font-family: "Cinzel", serif; font-weight: 600; font-size: 52px; line-height: 66px;
    color: var(--white); text-align: center; letter-spacing: 8px;
  }
</style>
</head>
<body>
<div class="canvas">
  <div class="cover">
    <section class="back">
      <div class="about-book">
        <h2 class="section-title">About the Book</h2>
        <p class="book-blurb">Gearstorm is a look at the rapidly changing face of robotics and how it will revolutionize employment over the next thirty years.<br>Tom Hale lays out the arguments in favor of and against the mechanization of our society, as well as the advantages and untold risks as we march into this ever-present future</p>
        <blockquote class="quote">A fascinating look into the future of robotics and their impact on humanity, be prepared to question when robots will replace you -<cite>Derek Lansford, Professor of Cybernetics at the University of Elmsworth</cite></blockquote>
      </div>
      <div class="about-author">
        <svg class="author-photo" role="img" aria-label="Black and white portrait photo of the author" viewBox="0 0 111 159">
          <defs><linearGradient id="photoTone" x1="0" y1="0" x2="0" y2="1"><stop offset="0" stop-color="#e6e6e6"/><stop offset="1" stop-color="#4a4a4a"/></linearGradient></defs>
          <rect width="111" height="159" fill="url(#photoTone)"/>
        </svg>
        <h2 class="section-title">About the Author</h2>
        <p class="author-name-back">TOM HALE</p>
        <div class="author-panel">
          <p>is a leading futurologist, technologist, inventor, and entrepreneur. With over twenty years of experience in technology and innovation, Tom has travelled the world seeking out and developing new technologies. As a leading voice on the challenges and benefits of tomorrow’s technology, he has advised some of the world’s leading institutions, including the Amber Hall, regarding technological preparations for the future. He is the recipient of the millennium entrepreneur of the year award and has appeared on numerous technology and philanthropy television programs, as well as presenting Steel Dawn Weekly on Robotics.</p>
        </div>
      </div>
    </section>

    <section class="spine">
      <div class="spine-text">
        <span class="spine-title"><b>GEARSTORM</b></span>
        <span class="spine-author">TOM HALE</span>
        <span class="spine-strap">THE END OF HUMAN JOBS AND HOW ROBOTS WILL REPLACE THEM</span>
      </div>
    </section>

    <section class="front">
      <div class="cover-art" role="img" aria-label="Glowing white robotic figure on a round pedestal, ringed by a spiral of blue light above a patterned floor"></div>
      <h1 class="front-title">Gearstorm</h1>
      <p class="strap">THE END OF HUMAN JOBS AND<br>HOW ROBOTS WILL REPLACE THEM</p>
      <div class="rule"></div>
      <p class="front-author">Tom Hale</p>
    </section>
  </div>
</div>
</body>
</html>
```